corvale institute of business and technology web site

I need web site for the institute which focus on business courses and computer course it is also for vocation train for employment It is also carear development and advancement .It should have links to online study resource which free
Industry/Entity Type
Business
Number of Pages Required
1 page
Look and feel
Each slider illustrates characteristics of the customer's brand and the style your logo design should communicate.

```html
<!DOCTYPE html>
<html lang="en">
<head>
<meta charset="utf-8">
<title>Corvale Institute of Business and Technology</title>
<link href="https://fonts.googleapis.com/css2?family=Open+Sans:ital,wght@0,400;0,600;0,700;0,800;1,400&display=swap" rel="stylesheet">
<style>
:root{
  --blue:#1b6fbd;
  --blue-dark:#0f5498;
  --orange:#f7941d;
  --green:#a3c13a;
  --ink:#333a40;
  --muted:#6b737a;
  --line:#dde2e6;
  --card:#e3e7ea;
  --panel:#eceff1;
  --footer:#3b4853;
  --footer-dark:#313d47;
  --white:#ffffff;
}
*{box-sizing:border-box;margin:0;padding:0}
html,body{width:1200px;height:3100px;overflow:hidden}
body{font-family:"Open Sans",Arial,sans-serif;color:var(--ink);background:var(--white);font-size:14px;line-height:1.5}
.wrap{width:1080px;margin:0 auto;position:relative}

/* header */
.site-header{height:180px;position:relative}
.brand{position:absolute;left:0;top:22px;display:flex;align-items:center;gap:14px}
.brand-square{width:64px;height:64px;background:var(--blue);border-radius:6px}
.brand-name{color:var(--blue);font-weight:800;font-size:19px;line-height:1.2;text-transform:uppercase;width:300px}
.top-contacts{position:absolute;left:420px;top:10px;display:flex;gap:40px}
.contact-item{display:flex;gap:8px;align-items:flex-start}
.contact-item svg{margin-top:2px}
.contact-label{font-weight:700;font-size:13px;color:var(--blue);text-transform:uppercase;display:block}
.contact-value{font-size:13px;color:var(--ink)}
.top-right{position:absolute;right:0;top:8px;width:240px}
.socials{display:flex;gap:6px;justify-content:flex-end}
.socials span{width:24px;height:24px;border-radius:50%;background:var(--blue)}
.search{margin-top:12px;height:30px;border:1px solid var(--line);display:flex;align-items:center;justify-content:space-between;padding:0 10px;font-size:12px;color:var(--muted)}
.main-nav{position:absolute;right:0;top:128px;display:flex;gap:0}
.main-nav a{display:block;padding:8px 16px;font-weight:700;font-size:14px;color:var(--ink);text-decoration:none;text-transform:uppercase}
.main-nav a.active{color:var(--white);background:var(--blue)}

/* slider */
.hero{height:420px;position:relative;overflow:hidden}
.hero-photo{position:absolute;inset:0;background:linear-gradient(180deg,#4e5a66 0%,#7d8a94 45%,#b9b2a4 100%)}
.hero-text{position:absolute;left:0;right:0;top:120px;text-align:center;color:var(--white)}
.hero-text h1{font-size:46px;font-weight:800;letter-spacing:.5px;text-transform:uppercase}
.hero-text p{font-size:19px;font-weight:700;margin-top:6px;line-height:1.35}
.btn-orange{display:inline-block;background:var(--orange);color:var(--white);font-weight:700;text-transform:uppercase;text-decoration:none;border-radius:3px}
.hero-text .btn-orange{margin-top:22px;padding:10px 26px;font-size:14px}
.hero-arrow{position:absolute;top:186px;width:34px;height:48px;background:rgba(20,30,40,.75);display:flex;align-items:center;justify-content:center}
.hero-arrow.left{left:0}
.hero-arrow.right{right:0}

/* welcome */
.welcome{height:400px;padding-top:70px}
.welcome .wrap{display:flex;justify-content:space-between}
.welcome-text{width:680px}
.section-title{color:var(--blue);font-weight:800;font-size:20px;line-height:1.25;text-transform:uppercase}
.welcome-text p{margin-top:16px;font-size:14px;line-height:1.75;color:var(--ink)}
.featured{width:320px;border:1px solid var(--line)}
.featured h3{font-size:17px;font-weight:800;text-transform:uppercase;padding:10px 14px;color:var(--ink);border-bottom:1px solid var(--line)}
.video{height:168px;margin:12px;position:relative;background:linear-gradient(135deg,#2c4a6b,#6f8aa3);display:flex;align-items:center;justify-content:center}
.featured p{padding:0 14px 14px;font-size:13px;color:var(--muted)}

/* programs */
.programs{height:480px;padding-top:20px}
.programs-head{display:flex;justify-content:space-between;align-items:center;border-bottom:2px solid var(--line);padding-bottom:8px}
.programs-head .arrows{display:flex;gap:12px}
.program-grid{display:flex;gap:24px;margin-top:18px}
.program-card{width:252px;height:300px;background:var(--card);padding:14px;position:relative;overflow:hidden}
.program-card h4{font-size:14px;font-weight:700;line-height:1.3;height:38px;color:var(--ink)}
.program-photo{height:120px;margin-top:8px}
.program-card p{font-size:12px;line-height:1.6;color:var(--muted);margin-top:12px}
.program-card .corner{position:absolute;right:0;bottom:0;width:0;height:0;border-left:26px solid transparent;border-bottom:26px solid var(--blue)}

/* online study */
.study{height:370px;position:relative}
.study-photo{position:absolute;inset:0;background:linear-gradient(180deg,#f4f2ee 0%,#e6e1d9 60%,#cfc7ba 100%)}
.study-text{position:absolute;left:100px;top:100px;width:520px;text-align:center}
.study-text h2{font-size:50px;font-weight:800;line-height:1.05;color:#3a3f45;text-transform:uppercase}
.study-text h3{font-size:27px;font-weight:700;color:#3a3f45;text-transform:uppercase;margin-top:6px}
.study-text .btn-orange{margin-top:18px;padding:10px 34px;font-size:20px;border-radius:4px}

/* people + question */
.engage{height:710px;padding-top:90px}
.engage .wrap{display:flex;justify-content:space-between}
.engage-left{width:600px}
.testimonial{text-align:center;padding:0 20px}
.testimonial h2{font-size:19px;font-weight:800;text-transform:uppercase;color:var(--ink);border-bottom:1px solid var(--line);padding-bottom:12px}
.quote-badge{width:46px;height:46px;border-radius:50%;background:var(--blue);margin:22px auto 0;display:flex;align-items:center;justify-content:center}
.testimonial blockquote{font-style:italic;font-size:14px;line-height:1.7;color:var(--muted);margin-top:16px}
.person{display:flex;align-items:center;justify-content:center;gap:10px;margin-top:18px;text-align:left}
.avatar{width:40px;height:40px;border-radius:50%;background:#c8a68c}
.person strong{display:block;font-size:13px;color:var(--ink)}
.person span{font-size:12px;color:var(--muted)}
.alerts{margin-top:40px;background:var(--panel);padding:26px 40px;text-align:center}
.alerts h2{color:var(--blue);font-size:20px;font-weight:800;text-transform:uppercase}
.alerts p{font-size:13px;color:var(--muted);margin-top:4px}
.subscribe{display:flex;margin-top:14px}
.subscribe .field{flex:1;height:38px;background:var(--white);border:1px solid var(--line);text-align:left;padding:8px 12px;font-size:13px;color:var(--muted)}
.subscribe .btn{background:var(--blue);color:var(--white);font-weight:700;font-size:14px;padding:8px 24px}
.question{width:400px;height:540px;background:var(--blue);padding:20px 30px;color:var(--white)}
.question h2{font-size:20px;font-weight:800;text-transform:uppercase;text-align:center;padding-bottom:12px;border-bottom:1px solid rgba(255,255,255,.3)}
.question label{display:block;font-size:13px;font-weight:700;margin-top:14px;margin-bottom:5px}
.input{background:var(--white);height:36px;font-size:13px;color:var(--muted);padding:7px 10px}
.row{display:flex;gap:10px}
.row .input{flex:1}
.input.area{height:110px}
.submit{margin-top:22px;background:var(--green);height:46px;text-align:center;font-weight:800;font-size:19px;line-height:46px;text-transform:uppercase}

/* footer */
.site-footer{height:560px;background:var(--footer);color:#c9d0d6;position:relative}
.footer-cols{display:flex;padding-top:60px}
.footer-col h5{color:var(--white);font-size:14px;font-weight:800;text-transform:uppercase;padding-bottom:10px;border-bottom:1px solid rgba(255,255,255,.2);margin-bottom:12px}
.footer-col ul{list-style:none}
.footer-col li{font-size:13px;line-height:1.9}
.col-nav{width:208px}
.col-prog{width:268px}
.col-news{width:332px}
.col-contact{width:272px}
.col-nav,.col-prog,.col-news{padding-right:40px}
.news-item{margin-bottom:12px}
.news-item .date{color:var(--orange);font-size:12px;display:block}
.news-item span{font-size:13px;line-height:1.5}
.contact-row{display:flex;gap:10px;margin-bottom:16px;font-size:13px;line-height:1.5}
.contact-row svg{flex:none;margin-top:3px}
.partner{position:absolute;left:60px;top:440px;display:flex;align-items:center;gap:16px}
.partner-label{color:var(--white);font-weight:800;font-size:15px;line-height:1.25;text-transform:uppercase}
.partner-name{background:#111;color:var(--white);font-weight:800;font-size:15px;text-transform:uppercase;padding:20px 18px}
.footer-socials{position:absolute;right:60px;top:452px;display:flex;gap:8px}
.footer-socials span{width:30px;height:30px;border-radius:50%;border:2px solid #c9d0d6}
.copyright{position:absolute;right:60px;top:510px;font-size:12px;color:#aab3ba}
</style>
</head>
<body>

<header class="site-header">
  <div class="wrap" style="height:180px">
    <div class="brand">
      <div class="brand-square"></div>
      <div class="brand-name">Corvale Institute of Business and Technology</div>
    </div>
    <div class="top-contacts">
      <div class="contact-item">
        <svg width="22" height="22" viewBox="0 0 22 22"><circle cx="11" cy="11" r="11" fill="#1b6fbd"/><path d="M7 6l2.5-.5 1.3 3-1.5 1a7 7 0 003.2 3.2l1-1.5 3 1.3-.5 2.5C10 15 7 12 7 6z" fill="#fff"/></svg>
        <div><span class="contact-label">Call us</span><span class="contact-value">+260 555 014 270</span></div>
      </div>
      <div class="contact-item">
        <svg width="22" height="22" viewBox="0 0 22 22"><circle cx="11" cy="11" r="11" fill="#1b6fbd"/><rect x="5.5" y="7" width="11" height="8" fill="none" stroke="#fff" stroke-width="1.4"/><path d="M5.5 7l5.5 4.5L16.5 7" fill="none" stroke="#fff" stroke-width="1.4"/></svg>
        <div><span class="contact-label">Email us</span><span class="contact-value">hello@corvaleinstitute.edu</span></div>
      </div>
    </div>
    <div class="top-right">
      <div class="socials"><span></span><span></span><span></span><span></span><span></span></div>
      <div class="search"><span>Search</span>
        <svg width="14" height="14" viewBox="0 0 14 14"><circle cx="6" cy="6" r="4.5" fill="none" stroke="#6b737a" stroke-width="1.6"/><path d="M9.5 9.5L13 13" stroke="#6b737a" stroke-width="1.6"/></svg>
      </div>
    </div>
    <nav class="main-nav">
      <a href="#" class="active">Home</a><a href="#">About us</a><a href="#">Courses</a><a href="#">Contact us</a>
    </nav>
  </div>
</header>

<section class="hero">
  <div class="hero-photo" role="img" aria-label="Photo of a study desk with laptop, notebook and coffee cup"></div>
  <div class="hero-text">
    <h1>Lorem ipsum dolor sit amet</h1>
    <p>Lorem ipsum dolor sit amet, consectetur adipiscing elit, sed do eiusmod<br>tempor.</p>
    <a href="#" class="btn-orange">Learn more</a>
  </div>
  <div class="hero-arrow left"><svg width="12" height="18" viewBox="0 0 12 18"><path d="M10 2L3 9l7 7" fill="none" stroke="#fff" stroke-width="3"/></svg></div>
  <div class="hero-arrow right"><svg width="12" height="18" viewBox="0 0 12 18"><path d="M2 2l7 7-7 7" fill="none" stroke="#fff" stroke-width="3"/></svg></div>
</section>

<section class="welcome">
  <div class="wrap">
    <div class="welcome-text">
      <h2 class="section-title">Welcome to<br>Corvale Institute of Business and Technology</h2>
      <p>Corvale Institute of Business and Technology is a fast growing Education &amp; Training Solution Provider, focusing on holistic knowledge and skills interventions that impact livelihoods. It is established on the core values of making a meaningful and measurable difference on career aspirations and goals through innovative learning and knowledge management interventions. We prepare students not only for professional success but also inculcate the importance of discipline and equip them physically, mentally, socially and spiritually. The institution is licensed and registered under the National Vocational Skills Authority (NVSA).</p>
    </div>
    <aside class="featured">
      <h3>Featured video</h3>
      <div class="video" role="img" aria-label="Video still of students in a classroom">
        <svg width="56" height="56" viewBox="0 0 56 56"><circle cx="28" cy="28" r="28" fill="#1b6fbd"/><path d="M22 17l17 11-17 11z" fill="#fff"/></svg>
      </div>
      <p>Lorem ipsum dolor sit amet, consectetur adipiscing elit.</p>
    </aside>
  </div>
</section>

<section class="programs">
  <div class="wrap">
    <div class="programs-head">
      <h2 class="section-title">Programs offered</h2>
      <div class="arrows">
        <svg width="12" height="16" viewBox="0 0 12 16"><path d="M10 1L3 8l7 7" fill="none" stroke="#333a40" stroke-width="3"/></svg>
        <svg width="12" height="16" viewBox="0 0 12 16"><path d="M2 1l7 7-7 7" fill="none" stroke="#333a40" stroke-width="3"/></svg>
      </div>
    </div>
    <div class="program-grid">
      <article class="program-card">
        <h4>University Education – Long Distance Learning</h4>
        <div class="program-photo" role="img" aria-label="Photo of graduates in caps and gowns" style="background:linear-gradient(135deg,#24354a,#6a7c8e)"></div>
        <p>Lorem ipsum dolor sit amet, consectetur adipiscing elit, sed do eiusmod tempor incididunt ut labore et dolore magna aliqua. Ut enim ad minim.</p>
        <span class="corner"></span>
      </article>
      <article class="program-card">
        <h4>Modular Soft Skills</h4>
        <div class="program-photo" role="img" aria-label="Photo of a business team meeting around a table" style="background:linear-gradient(135deg,#cfd6dc,#8a98a4)"></div>
        <p>Lorem ipsum dolor sit amet, consectetur adipiscing elit, sed do eiusmod tempor incididunt ut labore et dolore magna aliqua. Ut enim ad minim.</p>
        <span class="corner"></span>
      </article>
      <article class="program-card">
        <h4>Direct to Degree (D2D)</h4>
        <div class="program-photo" role="img" aria-label="Illustration of digital learning devices and icons" style="background:linear-gradient(135deg,#1f6fb4,#6cb2e3)"></div>
        <p>Lorem ipsum dolor sit amet, consectetur adipiscing elit, sed do eiusmod tempor incididunt ut labore et dolore magna aliqua. Ut enim ad minim.</p>
        <span class="corner"></span>
      </article>
      <article class="program-card">
        <h4>Skillcrest</h4>
        <div class="program-photo" role="img" aria-label="Photo of a professional presenting at a whiteboard" style="background:linear-gradient(135deg,#e9ecef,#9aa5ae)"></div>
        <p>Lorem ipsum dolor sit amet, consectetur adipiscing elit, sed do eiusmod tempor incididunt ut labore et dolore magna aliqua. Ut enim ad minim.</p>
        <span class="corner"></span>
      </article>
    </div>
  </div>
</section>

<section class="study">
  <div class="study-photo" role="img" aria-label="Photo of a bright desk with a laptop, desk lamp and books against a pale wall"></div>
  <div class="study-text">
    <h2>Online study</h2>
    <h3>Resource which free</h3>
    <a href="#" class="btn-orange">Click here</a>
  </div>
</section>

<section class="engage">
  <div class="wrap">
    <div class="engage-left">
      <div class="testimonial">
        <h2>What our people say</h2>
        <div class="quote-badge"><svg width="22" height="18" viewBox="0 0 22 18"><path d="M0 18V10C0 4 3 1 8 0l1 2C6 3 5 5 5 8h4v10zm13 0V10c0-6 3-9 8-10l1 2c-3 1-4 3-4 6h4v10z" fill="#fff"/></svg></div>
        <blockquote>“Lorem ipsum dolor sit amet, consectetur adipiscing elit, sed do eiusmod tempor incididunt ut labore et dolore magna aliqua. Ut enim ad minim veniam, quis nostrud exercitation ullamco laboris nisi ut aliquip ex ea commodo consequat.”</blockquote>
        <div class="person">
          <div class="avatar" role="img" aria-label="Portrait of the student"></div>
          <div><strong>Dana Holloway</strong><span>Former student</span></div>
        </div>
      </div>
      <div class="alerts">
        <h2>Auction alerts!</h2>
        <p>Sign up to receive email alerts about our upcoming auctions</p>
        <div class="subscribe"><div class="field">Enter your email address</div><div class="btn">Subscribe</div></div>
      </div>
    </div>
    <form class="question">
      <h2>Do you have a question?</h2>
      <label>Your Name*</label>
      <div class="row"><div class="input">First Name</div><div class="input">Last Name</div></div>
      <label>Email*</label>
      <div class="input">Your Email Address Here</div>
      <label>Phone</label>
      <div class="input">Phone Number</div>
      <label>Comments*</label>
      <div class="input area"></div>
      <div class="submit">Submit</div>
    </form>
  </div>
</section>

<footer class="site-footer">
  <div class="wrap footer-cols">
    <div class="footer-col col-nav">
      <h5>Navigation</h5>
      <ul><li>Home</li><li>About Us</li><li>Courses</li><li>Contact Us</li></ul>
    </div>
    <div class="footer-col col-prog">
      <h5>Programs offered</h5>
      <ul><li>University Education – Long Distance Learning</li><li>Modular Soft Skills</li><li>Direct to Degree (D2D)</li><li>Skillcrest</li><li>Skillcrest Career Advancement</li><li>Business Vocation Training</li><li>Computer Technology Courses</li></ul>
    </div>
    <div class="footer-col col-news">
      <h5>Recent news</h5>
      <div class="news-item"><span class="date">January 20, 2015</span><span>Lorem ipsum dolor sit amet, consectetur adipiscing elit.</span></div>
      <div class="news-item"><span class="date">January 14, 2015</span><span>Lorem ipsum dolor sit amet, consectetur adipiscing elit.</span></div>
      <div class="news-item"><span class="date">January 08, 2015</span><span>Lorem ipsum dolor sit amet, consectetur adipiscing elit.</span></div>
    </div>
    <div class="footer-col col-contact">
      <h5>Contact info</h5>
      <div class="contact-row"><svg width="12" height="16" viewBox="0 0 12 16"><path d="M6 0a6 6 0 00-6 6c0 4.5 6 10 6 10s6-5.5 6-10a6 6 0 00-6-6zm0 8.5A2.5 2.5 0 116 3.5a2.5 2.5 0 010 5z" fill="#f7941d"/></svg><span>14 Harrowgate Plaza, Elmfield Road, Northbrook</span></div>
      <div class="contact-row"><svg width="14" height="14" viewBox="0 0 14 14"><path d="M1 2l3-1 2 3.5-2 1.5a8 8 0 004 4l1.5-2L13 10l-1 3C5 13 1 9 1 2z" fill="#f7941d"/></svg><span>Phone<br>+260 555 014 270, +260 555 014 271</span></div>
      <div class="contact-row"><svg width="14" height="12" viewBox="0 0 14 12"><rect x="1" y="1" width="12" height="10" fill="none" stroke="#f7941d" stroke-width="1.5"/><path d="M1 1l6 5 6-5" fill="none" stroke="#f7941d" stroke-width="1.5"/></svg><span>hello@corvaleinstitute.edu</span></div>
    </div>
  </div>
  <div class="partner">
    <div class="partner-label">In conjunction<br>with Skillcrest</div>
    <div class="partner-name">Skillcrest</div>
  </div>
  <div class="footer-socials"><span></span><span></span><span></span><span></span><span></span></div>
  <div class="copyright">© 2015 Corvale Institute of Business and Technology. All Rights Reserved.</div>
</footer>

</body>
</html>
```